Luxury Business Card Design for High-End Window Treatments

Gilded Slatworks
Custom Plantation Shutters & Architectural Shading Systems

⸻

BACK

Daniel Trevick
Owner

Custom Interior & Exterior Window Treatments

919-555-0148
gildedslatworks.com

I have included a picture that I’m hoping we can use on the back, but I’m also wondering if you can get rid of the ladder? Should we get rid of shutters , shades and blinds underneath Gilded Slatworks?

Target Market(s)

High-end residential homeowners, custom home builders, architects, interior designers, and luxury renovation clients seeking premium plantation shutters and motorized architectural shading systems.

Industry/Entity Type

Custom Window treatments

Contact Information for Business Card

Front Gilded Slatworks Custom Plantation Shutters Motorized Architectural Shading Systems BACK Daniel Trevick Owner 919-555-0148 GildedSlatworks.com Custom Interior & Exterior Window Treatments By Appointment

Requirements
Nice to have
• Not 100% sure on nice to halves or the color but you can definitely check out my website to get a better understanding of what I’m trying to do

```html
<!DOCTYPE html>
<html lang="en">
<head>
<meta charset="utf-8">
<title>Gilded Slatworks – Business Card</title>
<link rel="stylesheet" href="https://fonts.googleapis.com/css2?family=Cormorant+Garamond:wght@500&family=Hind:wght@500&family=Libre+Caslon+Text:wght@700&family=Montserrat:wght@400&display=swap">
<style>
  :root {
    --backdrop: #e6e6e8;
    --card-black: #000000;
    --cream: #efe7d3;
    --gold-name: #c4ad63;
    --gold-accent: #e2c85a;
    --gold-text: #d8c06a;
    --stripe: #8f8a3d;
    --white: #ffffff;
  }
  * { box-sizing: border-box; margin: 0; padding: 0; }
  html, body { width: 1200px; height: 1108px; overflow: hidden; }
  body { background: var(--backdrop); position: relative; font-family: "Montserrat", sans-serif; }

  .card { position: absolute; overflow: hidden; }
  .card--front { left: 222px; top: 51px; width: 786px; height: 480px; background: var(--card-black); }
  .card--back { left: 220px; top: 577px; width: 788px; height: 463px; }

  .card__art { position: absolute; inset: 0; }

  .brand { position: absolute; text-align: center; }
  .brand__name {
    font-family: "Cormorant Garamond", serif; font-weight: 500;
    color: var(--cream); line-height: 1;
  }
  .brand__tagline {
    font-family: "Hind", sans-serif; font-weight: 500;
    color: var(--gold-accent); word-spacing: 10px;
  }

  .card--front .brand { left: 40px; top: 52px; width: 210px; }
  .card--front .brand__name { font-size: 40px; }
  .card--front .brand__tagline { font-size: 16px; margin-top: 12px; }

  .contact { position: absolute; left: 38px; top: 208px; color: var(--white); }
  .contact__name {
    font-family: "Libre Caslon Text", serif; font-weight: 700;
    font-size: 29px; color: var(--gold-name); line-height: 1.1;
  }
  .contact__role { font-size: 17px; margin-top: 4px; }
  .contact__services { font-size: 17px; line-height: 21px; margin-top: 20px; }
  .contact__list { list-style: none; margin-top: 22px; }
  .contact__item { display: flex; align-items: center; gap: 10px; font-size: 17px; height: 29px; }
  .contact__icon { width: 18px; height: 18px; flex: none; }
  .contact__note { font-size: 17px; color: var(--gold-text); margin-top: 9px; }

  .card--back .brand { left: 500px; top: 110px; width: 240px; }
  .card--back .brand__name { font-size: 38px; }
  .card--back .brand__tagline { font-size: 14px; margin-top: 12px; word-spacing: 8px; }
</style>
</head>
<body>

<section class="card card--front" aria-label="Business card front">
  <svg class="card__art" viewBox="0 0 786 480" width="786" height="480">
    <defs>
      <linearGradient id="frontPhoto" x1="0" y1="0" x2="0" y2="1">
        <stop offset="0" stop-color="#7aa6d6"/>
        <stop offset="0.3" stop-color="#9aa59a"/>
        <stop offset="0.55" stop-color="#3d3f48"/>
        <stop offset="0.8" stop-color="#5b6248"/>
        <stop offset="1" stop-color="#7c7556"/>
      </linearGradient>
    </defs>
    <polygon points="466,0 786,0 786,480 336,480" fill="url(#frontPhoto)"
             role="img" aria-label="Photo of a covered porch with dark exterior shades and lawn chairs"/>
    <polygon points="466,0 478,0 348,480 336,480" fill="var(--stripe)"/>
  </svg>

  <div class="brand">
    <p class="brand__name">Gilded<br>Slatworks</p>
    <p class="brand__tagline">Shutters Shades Blinds</p>
  </div>

  <div class="contact">
    <h1 class="contact__name">Daniel Trevick</h1>
    <p class="contact__role">Owner</p>
    <p class="contact__services">Custom Interior &amp; Exterior<br>Window Treatments</p>
    <ul class="contact__list">
      <li class="contact__item">
        <svg class="contact__icon" viewBox="0 0 18 18" aria-hidden="true">
          <path d="M2 6 Q9 1 16 6 L14 8 L12 6 L6 6 L4 8 Z" fill="var(--gold-text)"/>
          <rect x="3" y="9" width="12" height="7" rx="1" fill="var(--gold-text)"/>
        </svg>
        919-555-0148
      </li>
      <li class="contact__item">
        <svg class="contact__icon" viewBox="0 0 18 18" aria-hidden="true">
          <circle cx="9" cy="9" r="7.5" fill="var(--gold-text)"/>
          <path d="M5 5 Q8 7 7 10 Q10 11 9 15 M12 4 Q11 7 14 9" stroke="#000" stroke-width="1.5" fill="none"/>
        </svg>
        GildedSlatworks.com
      </li>
    </ul>
    <p class="contact__note">By Appointment</p>
  </div>
</section>

<section class="card card--back" aria-label="Business card back">
  <svg class="card__art" viewBox="0 0 788 463" width="788" height="463">
    <defs>
      <linearGradient id="backPhoto" x1="0" y1="0" x2="0" y2="1">
        <stop offset="0" stop-color="#7ea9d8"/>
        <stop offset="0.25" stop-color="#a7ad9c"/>
        <stop offset="0.33" stop-color="#30323c"/>
        <stop offset="0.55" stop-color="#2c2f38"/>
        <stop offset="0.75" stop-color="#5f6553"/>
        <stop offset="1" stop-color="#6f7055"/>
      </linearGradient>
    </defs>
    <rect width="788" height="463" fill="url(#backPhoto)"
          role="img" aria-label="Photo of a two-storey covered porch fitted with dark exterior shades, garden and lawn chairs"/>
  </svg>

  <div class="brand">
    <p class="brand__name">Gilded<br>Slatworks</p>
    <p class="brand__tagline">Shutters Shades Blinds</p>
  </div>
</section>

</body>
</html>
```